Heron Loan Partners Business Card

We need a business card design for our mortgage servicing company. In addition to servicing the loans of homeowners, we help homeowners with purchasing their homes and any mortgage refinancing. We would like to see designs that use the colors in the logo attached below (gold-ish yellow and navy blue), and any other design you deem fit! The design should communicate a simpler life with smart mortgages provided by Heron.

```html
<!DOCTYPE html>
<html lang="en">
<head>
<meta charset="utf-8">
<title>Heron Loan Partners – Business Card</title>
<link rel="stylesheet" href="https://fonts.googleapis.com/css2?family=Open+Sans:wght@400;700&display=swap">
<style>
  :root {
    --gold: #e1b140;
    --navy: #241f52;
    --white: #ffffff;
    --stage: #222222;
  }
  * { margin: 0; padding: 0; box-sizing: border-box; }
  html, body {
    width: 1200px; height: 780px; overflow: hidden;
    background: var(--stage);
    font-family: "Open Sans", Arial, sans-serif;
  }
  .sheet {
    position: relative; width: 1200px; height: 780px;
    display: flex; flex-direction: column; align-items: center;
    justify-content: center; gap: 24px;
  }
  .card {
    position: relative; width: 620px; height: 354px;
    border-radius: 22px; overflow: hidden;
  }
  .card--front { background: var(--gold); }
  .card--back { background: var(--white); }

  .brand {
    position: absolute; display: flex; align-items: center; gap: 12px;
    color: var(--navy); font-weight: 700; white-space: nowrap;
  }
  .brand__dot { border-radius: 50%; background: var(--navy); flex: none; }
  .card--front .brand {
    left: 50%; top: 50%; transform: translate(-50%, -50%);
    font-size: 40px;
  }
  .card--front .brand__dot { width: 26px; height: 26px; }
  .card--back .brand { right: 48px; top: 58px; font-size: 24px; gap: 9px; }
  .card--back .brand__dot { width: 16px; height: 16px; background: var(--gold); }

  .waves { position: absolute; inset: 0; width: 100%; height: 100%; }
  .wave--navy { fill: var(--navy); }
  .wave--gold { fill: var(--gold); }

  .contact {
    position: absolute; left: 64px; top: 200px; color: var(--white);
  }
  .contact__name { color: var(--gold); font-weight: 700; font-size: 22px; line-height: 26px; }
  .contact__role { font-size: 13px; line-height: 18px; margin-bottom: 8px; }
  .contact__address { font-size: 12.5px; line-height: 17px; margin-bottom: 8px; }
  .contact__list { list-style: none; font-size: 12.5px; line-height: 17px; }
  .contact__list li { display: flex; align-items: center; gap: 8px; }
  .contact__icon { width: 11px; height: 11px; fill: var(--gold); flex: none; }
</style>
</head>
<body>
<main class="sheet">
  <section class="card card--front" aria-label="Card front">
    <div class="brand"><span class="brand__dot"></span>Heron Loan Partners</div>
  </section>

  <section class="card card--back" aria-label="Card back">
    <div class="brand"><span class="brand__dot"></span>Heron Loan Partners</div>
    <svg class="waves" viewBox="0 0 620 354" preserveAspectRatio="none" aria-hidden="true">
      <path class="wave--navy" d="M0,178 C180,140 420,160 620,104 L620,124 C420,178 200,160 0,184 Z"/>
      <path class="wave--gold" d="M0,190 C160,162 400,178 620,138 L620,150 C400,190 180,178 0,204 Z"/>
      <path class="wave--navy" d="M0,212 C170,178 420,190 620,160 L620,354 L0,354 Z"/>
    </svg>
    <div class="contact">
      <p class="contact__name">Lena Marek</p>
      <p class="contact__role">Co-Founder</p>
      <p class="contact__address">418 Lakeside Ave. Suite 310<br>Granbury, TX 76048</p>
      <ul class="contact__list">
        <li><svg class="contact__icon" viewBox="0 0 24 24"><path d="M6.6 10.8a15.1 15.1 0 0 0 6.6 6.6l2.2-2.2a1 1 0 0 1 1-.25 11.4 11.4 0 0 0 3.6.57 1 1 0 0 1 1 1V20a1 1 0 0 1-1 1A17 17 0 0 1 3 4a1 1 0 0 1 1-1h3.5a1 1 0 0 1 1 1c0 1.25.2 2.45.57 3.57a1 1 0 0 1-.25 1z"/></svg>(555) 214-6093</li>
        <li><svg class="contact__icon" viewBox="0 0 24 24"><path d="M2 5h20v14H2z M2 5l10 8 10-8" fill="none" stroke="#e1b140" stroke-width="2.5"/></svg>info@heronloan.com</li>
        <li><svg class="contact__icon" viewBox="0 0 24 24"><circle cx="12" cy="12" r="10" fill="none" stroke="#e1b140" stroke-width="2.5"/><path d="M2 12h20M12 2c3 3 3 17 0 20M12 2c-3 3-3 17 0 20" fill="none" stroke="#e1b140" stroke-width="2"/></svg>www.heronloan.com</li>
      </ul>
    </div>
  </section>
</main>
</body>
</html>
```